Fresh, modern, fun business card for pediatric dental practice

Need a business card for fresh, modern, fun pediatric dental practice

Clean look that matches our website's font and colors

We prefer the look of curved corners on business cards

Target Market(s)

parents (mothers) of young children, professionals, mid-high class

Industry/Entity Type

Dental

Contact Information for Business Card

Maplebrook Pediatric Dentistry
482 Quarry Lane
Suite 517
Oakvale, PA 17590
717.555.0193
www.maplebrookkidsdental.example

Mei-Ran Tsai, DMD
Corinne Walbeck, DMD
(we are working on our email address, but we would like that on the card as well)

Font styles to use
Sans Serif

Requirements
Must have
• All info; we would also like to make cards for individual staff members
• colors from our website and color palatte, attatched
• use same font and design as website for branding
Nice to have
• clean, simple card that has a pop of color
• we would like to see a few designs with our tag line "where smiles get brighter"
• we are not sure if we want to have it on there or not
• we would like to see a few designs incorporating the ribbon graphic on our website where the word WELCOME is

```html
<!DOCTYPE html>
<html lang="en">
<head>
<meta charset="utf-8">
<title>Maplebrook Pediatric Dentistry — Business Card</title>
<link rel="stylesheet" href="https://fonts.googleapis.com/css2?family=Roboto:wght@400;500&family=Roboto+Condensed:wght@700&display=swap">
<style>
  :root {
    --backdrop: #2a2a2a;
    --magenta: #c8318b;
    --sun: #f0b323;
    --paper: #f3f3f3;
    --ink-white: #ffffff;
    --ink-grey: #4a4a4a;
  }
  * { margin: 0; padding: 0; box-sizing: border-box; }
  html, body {
    width: 1200px; height: 960px; overflow: hidden;
    background: var(--backdrop);
    font-family: "Roboto", Arial, sans-serif;
  }
  .stage { position: relative; width: 1200px; height: 960px; }

  .card {
    position: absolute; width: 600px; height: 343px;
    border-radius: 20px; overflow: hidden; background: var(--paper);
  }
  .card--front { left: 314px; top: 113px; }
  .card--back  { left: 311px; top: 472px; }

  .front-panel {
    position: absolute; left: 0; top: 0; width: 289px; height: 100%;
    background: var(--magenta);
  }
  .front-edge {
    position: absolute; right: 0; top: 0; width: 17px; height: 100%;
    background: var(--sun);
  }

  .dentists {
    position: absolute; left: 34px; top: 73px;
    font-family: "Roboto Condensed", "Arial Narrow", sans-serif;
    font-weight: 700; font-size: 21px; line-height: 24px;
    color: var(--sun); letter-spacing: -0.2px;
  }
  .address {
    position: absolute; left: 34px; top: 148px;
    font-size: 14.5px; line-height: 18px; color: var(--ink-white);
    font-style: normal;
  }
  .contact { position: absolute; left: 34px; top: 231px; list-style: none; }
  .contact li {
    display: flex; align-items: center; gap: 6px;
    font-size: 14.5px; line-height: 19.5px; color: var(--ink-white);
  }
  .contact svg { width: 13px; height: 13px; flex: none; }

  .brand {
    position: absolute; text-align: center;
    font-family: "Roboto", Arial, sans-serif; font-weight: 500;
    color: var(--sun);
  }
  .brand-dot { display: block; margin: 0 auto 12px; border-radius: 50%; background: var(--sun); }
  .brand--front { left: 289px; width: 294px; top: 108px; font-size: 27px; line-height: 32px; }
  .brand--front .brand-dot { width: 44px; height: 44px; }
  .brand--back { left: 0; width: 600px; top: 98px; font-size: 34px; line-height: 40px; }
  .brand--back .brand-dot { width: 56px; height: 56px; }

  .back-url {
    position: absolute; left: 0; width: 600px; top: 295px; text-align: center;
    font-size: 14px; letter-spacing: 3.4px; color: var(--ink-grey);
  }
</style>
</head>
<body>
<main class="stage">
  <section class="card card--front">
    <div class="front-panel">
      <p class="dentists">Mei-Ran Tsai, DMD<br>Corinne Walbeck, DMD</p>
      <address class="address">
        Maplebrook Pediatric Dentistry<br>
        482 Quarry Lane<br>
        Suite 517<br>
        Oakvale, PA 17590
      </address>
      <ul class="contact">
        <li>
          <svg viewBox="0 0 16 16" aria-hidden="true"><path fill="#f0b323" d="M3.6 1.2l2.3-.4 1.3 3.4-1.6 1.2c.8 1.8 2.2 3.3 4 4.1l1.3-1.6 3.3 1.3-.4 2.4c-.2.9-1 1.4-1.9 1.3C6.4 12.4 2.6 8.6 2.1 3.1c-.1-.9.5-1.7 1.5-1.9z"/></svg>
          717.555.0193
        </li>
        <li>
          <svg viewBox="0 0 16 16" aria-hidden="true"><circle cx="8" cy="8" r="7" fill="#f0b323"/><path fill="none" stroke="#c8318b" stroke-width="1.2" d="M5 3.5c1 1 .5 2 1.5 2.5s1 1.5 0 2.5M10 10c1-.5 2-.2 2.5.8M9.5 3c-.5 1 .5 1.5 1.5 1.5"/></svg>
          maplebrookkidsdental.example
        </li>
      </ul>
    </div>
    <div class="brand brand--front">
      <span class="brand-dot" aria-hidden="true"></span>
      Maplebrook<br>Pediatric Dentistry
    </div>
    <div class="front-edge"></div>
  </section>

  <section class="card card--back">
    <div class="brand brand--back">
      <span class="brand-dot" aria-hidden="true"></span>
      Maplebrook<br>Pediatric Dentistry
    </div>
    <p class="back-url">www.maplebrookkidsdental.example</p>
  </section>
</main>
</body>
</html>
```